Sleep/Snoring Business - Requires Website - Australia

We are seeking a simple to maintain website for our sleep business. The health care business provides diagnostic and treatment solutions for snoring, sleep disorders and other respiratory problems.

Ideally, colours to match the company logo (attached).

The page must be built using WORDPRESS.

Ideally site will have a home page outlining the business, with 5 sub pages - being "Diagnosis" "Treatment Options", "Prodcuts", "About Us", "Contact Us"

The site home page should include a large picture on the home page.

The "Treatment Options" and "Diagnosis" pages must include:
Allow for a few pictures with assocaited text, plus space for some embeded youtube videos.

"Prodcuts" page should have the ability to show 3-4 products across the page with text below.. that can include external URL to products

The "About Us" page must include:
1. a Map (google map) to identify the various locations. There are 6 in total.
2. A Section to describe our doctors/staff - allow for a picture and some text

The "Contact Us" page must include:
email form
telephone details

The overall design should have a clean and medical/safe feeling

Target Market(s)

People who snore and those with sleeping and respiratory disorders

Industry/Entity Type

Health Care

Coding

Coded - Design and coding required

Number of Pages Required

5+ page

Colors

Designer to choose colors to be used in the design.

Requirements
Must have
• The page must be built using WORDPRESS.
• Ideally site will have a home page outlining the business, with 5 sub pages - being "Diagnosis" "Treatment Options", "Prodcuts", "About Us", "Contact Us"
• The site home page should include a large picture on the home page.
• The "Treatment Options" and "Diagnosis" pages must include:
• Allow for a few pictures with assocaited text, plus space for some embeded youtube videos.
• "Prodcuts" page should have the ability to show 3-4 products across the page with text below.. that can include external URL to products
• The "About Us" page must include:
• 1. a Map (google map) to identify the various locations. There are 6 in total.
• 2. A Section to describe our doctors/staff - allow for a picture and some text
• The "Contact Us" page must include:
• email form
• telephone details
• Pictures must be licenced or free to use
Nice to have
• Home page pictures showing people sleeping well, snoring or fresh air (landscape) type transition pictures (at least 3).
Should not have
• Not to look cheap
• This is a high end healthcare business, so must look that way

```html
<!DOCTYPE html>
<html lang="en">
<head>
<meta charset="utf-8">
<title>Restwell Clinic</title>
<link rel="stylesheet" href="https://fonts.googleapis.com/css2?family=Open+Sans:wght@400;600;700;800&display=swap">
<style>
:root{
  --navy:#0f3b6e;
  --blue:#1f5fa3;
  --sky:#2d7cc4;
  --pale:#eef3f9;
  --ink:#3c4650;
  --muted:#7b858f;
  --footer:#3a3d42;
  --footer-dark:#2f3236;
  --white:#ffffff;
}
*{box-sizing:border-box;margin:0;padding:0}
html,body{width:1200px;height:2812px;overflow:hidden;background:var(--white)}
body{font-family:"Open Sans",Arial,sans-serif;color:var(--ink);position:relative}
.site-header{position:absolute;top:0;left:0;width:1200px;height:100px;background:var(--white);box-shadow:0 2px 6px rgba(0,0,0,.08);z-index:3}
.brand{position:absolute;left:40px;top:26px;font-size:34px;font-weight:700;color:var(--navy);letter-spacing:.5px}
.main-nav{position:absolute;right:40px;top:0;height:100px;display:flex}
.main-nav a{display:flex;align-items:center;padding:0 26px;font-size:14px;font-weight:600;color:var(--navy);text-decoration:none;letter-spacing:.5px}
.main-nav a.active{background:var(--navy);color:var(--white)}
.hero{position:absolute;top:100px;left:0;width:1200px;height:620px;background:linear-gradient(180deg,#4b5f78 0%,#6f8198 45%,#8a98ab 100%)}
.hero-photo{position:absolute;inset:0}
.hero-text{position:absolute;top:70px;width:100%;text-align:center;color:var(--white)}
.hero-text h1{font-size:52px;font-weight:700;letter-spacing:1px}
.hero-text p{font-size:20px;margin-top:8px}
.btn-ghost{display:inline-block;margin-top:30px;padding:10px 22px;border:2px solid var(--white);color:var(--white);font-size:14px;font-weight:600;background:rgba(0,0,0,.25)}
.hero-arrow{position:absolute;top:220px;width:24px;height:40px}
.hero-curve{position:absolute;top:0;left:0}
.service{position:absolute;width:170px;height:170px;border-radius:50%;border:7px solid var(--white);box-shadow:0 4px 14px rgba(0,0,0,.3);display:flex;flex-direction:column;align-items:center;justify-content:center;color:var(--white);font-size:15px;font-weight:700;text-transform:uppercase;text-align:center}
.service svg{margin-bottom:14px}
.service.blue{background:var(--sky)}
.service.dark{background:#3c4552}
.section-title{position:absolute;width:100%;text-align:center;font-size:30px;font-weight:700;color:var(--navy)}
.section-title::after{content:"";display:block;width:70px;height:3px;background:var(--sky);margin:14px auto 0}
.lead{position:absolute;left:220px;width:760px;text-align:center;font-size:14px;line-height:22px;color:var(--muted)}
.intro{position:absolute;left:100px;top:1110px;width:660px}
.intro h2{font-size:22px;line-height:32px;color:var(--blue);font-weight:700}
.intro p{font-size:14px;line-height:23px;color:var(--muted);margin-top:20px}
.intro-art{position:absolute;left:810px;top:1110px;width:300px;height:240px;border-radius:8px;background:linear-gradient(160deg,#fde2c6,#9fd3ef)}
.diag-band{position:absolute;top:1460px;left:0;width:1200px;height:300px;background:linear-gradient(90deg,#0f3b6e,#24609f)}
.diag-text{position:absolute;left:100px;top:72px;width:460px;color:var(--white)}
.diag-text h2{font-size:28px;font-weight:700}
.diag-text p{font-size:14px;line-height:22px;margin-top:16px;opacity:.85}
.btn-line{display:inline-block;margin-top:26px;padding:8px 18px;border:2px solid var(--white);font-size:13px;font-weight:600}
.video{position:absolute;left:660px;top:40px;width:440px;height:230px;background:linear-gradient(180deg,#c9d3dd,#8d9bab);box-shadow:0 6px 20px rgba(0,0,0,.35)}
.video-bar{position:absolute;left:0;bottom:0;width:100%;height:24px;background:rgba(20,30,45,.75)}
.testimonial{position:absolute;top:2060px;width:280px}
.avatar{width:130px;height:130px;border-radius:50%;margin:0 auto;border:5px solid var(--white);box-shadow:0 0 0 2px #d5dbe2;background:linear-gradient(180deg,#d8c3b0,#a98c76)}
.quote-mark{font-size:54px;line-height:40px;color:var(--blue);font-weight:800;margin-top:34px}
.testimonial p{font-size:14px;line-height:22px;color:var(--muted)}
.testimonial .name{margin-top:14px;font-size:14px;color:var(--blue);font-weight:600}
.site-footer{position:absolute;top:2560px;left:0;width:1200px;height:252px;background:var(--footer);color:var(--white)}
.footer-brand{position:absolute;top:30px;width:100%;text-align:center;font-size:30px;font-weight:700}
.footer-contact{position:absolute;top:98px;width:100%;display:flex;justify-content:center;gap:50px;font-size:15px}
.footer-contact span{display:flex;align-items:center;gap:12px}
.icon-ring{width:34px;height:34px;border:2px solid var(--white);border-radius:50%;display:flex;align-items:center;justify-content:center}
.footer-nav{position:absolute;top:170px;width:100%;display:flex;justify-content:center;font-size:13px;font-weight:600}
.footer-nav a{color:var(--white);text-decoration:none;padding:0 22px;border-left:1px solid #777}
.footer-nav a:first-child{border-left:none}
.footer-bar{position:absolute;bottom:0;left:0;width:100%;height:44px;background:var(--footer-dark);display:flex;align-items:center;justify-content:space-between;padding:0 40px;font-size:12px}
.socials{display:flex;gap:10px;align-items:center}
.socials i{display:block;width:26px;height:26px;border:2px solid var(--white);border-radius:50%}
</style>
</head>
<body>

<header class="site-header">
  <div class="brand">Restwell</div>
  <nav class="main-nav">
    <a class="active">HOME</a><a>DIAGNOSIS</a><a>TREATMENT OPTIONS</a><a>ABOUT US</a><a>CONTACT US</a>
  </nav>
</header>

<section class="hero">
  <div class="hero-photo" role="img" aria-label="Photo of a couple sleeping in bed, one person snoring"></div>
  <div class="hero-text">
    <h1>RESTWELL CLINIC</h1>
    <p>Australia's premier sleep disorder specialists</p>
    <span class="btn-ghost">Read More</span>
  </div>
  <svg class="hero-arrow" style="left:20px" viewBox="0 0 24 40"><path d="M20 4 4 20l16 16" fill="none" stroke="#fff" stroke-width="3"/></svg>
  <svg class="hero-arrow" style="right:20px" viewBox="0 0 24 40"><path d="M4 4l16 16L4 36" fill="none" stroke="#fff" stroke-width="3"/></svg>
</section>

<svg class="hero-curve" width="1200" height="900" viewBox="0 0 1200 900" style="z-index:1">
  <path d="M0 580 Q600 820 1200 580 L1200 900 L0 900 Z" fill="#fff"/>
  <path d="M0 580 Q600 820 1200 580" fill="none" stroke="#1f5fa3" stroke-width="16"/>
  <path d="M0 596 Q600 836 1200 596" fill="none" stroke="#bcd3ea" stroke-width="4"/>
</svg>

<div class="service blue" style="left:155px;top:572px;z-index:2">
  <svg width="44" height="30" viewBox="0 0 44 30"><path d="M4 22c6 0 8-10 14-10s8 10 14 10 6-6 8-6" fill="none" stroke="#fff" stroke-width="3"/></svg>Snoring</div>
<div class="service dark" style="left:375px;top:610px;z-index:2">
  <svg width="34" height="40" viewBox="0 0 34 40"><rect x="3" y="5" width="28" height="33" rx="3" fill="none" stroke="#fff" stroke-width="3"/><path d="M9 16h16M9 23h16M9 30h10" stroke="#fff" stroke-width="3"/></svg>Diagnosis</div>
<div class="service dark" style="left:635px;top:612px;z-index:2">
  <svg width="44" height="40" viewBox="0 0 44 40"><path d="M22 4v18M22 18c-4-2-8 0-12 4-4 6-6 14-2 14s14-4 14-14M22 18c4-2 8 0 12 4 4 6 6 14 2 14s-14-4-14-14" fill="none" stroke="#fff" stroke-width="3"/></svg>Respiratory</div>
<div class="service blue" style="left:895px;top:572px;z-index:2">
  <svg width="48" height="34" viewBox="0 0 48 34"><path d="M4 4v26M4 22h40v8M14 14h28a4 4 0 0 1 4 4v4" fill="none" stroke="#fff" stroke-width="3"/><circle cx="11" cy="15" r="4" fill="#fff"/></svg>Sleep Disorders</div>

<h2 class="section-title" style="top:990px">WELCOME TO RESTWELL</h2>
<p class="lead" style="top:1050px">Our clinic helps adults and children rest easier through careful assessment, clear advice and proven care. From the first consultation to ongoing support, our specialists work with you to understand your sleep and find the treatment that suits your life and health.</p>

<section class="intro" style="top:1150px">
  <h2>We provide diagnostic and treatment solutions for snoring, sleep disorders and other respiratory problems.</h2>
  <p>Each patient begins with a detailed review of symptoms, history and lifestyle. Our team then recommends the right study, whether at home or in clinic, so that a diagnosis is accurate and treatment can start without delay. We explain every result in plain language and stay in touch as your sleep improves over the following months.</p>
  <p>Treatment options range from simple changes and oral devices to airway pressure therapy, each fitted and reviewed by experienced clinicians who care about lasting results.</p>
</section>
<div class="intro-art" style="top:1150px" role="img" aria-label="Illustration of a child covering her ears beside a snoring child in bed"></div>

<section class="diag-band">
  <div class="diag-text">
    <h2>DIAGNOSTIC TECHNIQUES</h2>
    <p>Modern sleep studies measure breathing, oxygen, heart rate and movement through the night. Results guide a plan built around you.</p>
    <span class="btn-line">JOIN WITH US</span>
  </div>
  <div class="video" role="img" aria-label="Video still of a man snoring in bed">
    <div class="video-bar"></div>
  </div>
</section>

<h2 class="section-title" style="top:1940px">OUR TESTIMONIALS</h2>

<article class="testimonial" style="left:100px">
  <div class="avatar" role="img" aria-label="Portrait of a smiling woman"></div>
  <div class="quote-mark">&ldquo;</div>
  <p>After years of loud snoring I finally sleep through the night, and my partner does too. The team was kind and thorough.</p>
  <div class="name">&ndash; Clara</div>
</article>
<article class="testimonial" style="left:460px">
  <div class="avatar" role="img" aria-label="Portrait of a smiling man"></div>
  <div class="quote-mark">&ldquo;</div>
  <p>The home study was easy to set up and the results were explained clearly. I wake up rested and ready for the day.</p>
  <div class="name">&ndash; Daniel</div>
</article>
<article class="testimonial" style="left:820px">
  <div class="avatar" role="img" aria-label="Portrait of a smiling woman"></div>
  <div class="quote-mark">&ldquo;</div>
  <p>Friendly staff, quick appointments and a treatment that actually works. I would recommend this clinic to anyone struggling with sleep.</p>
  <div class="name">&ndash; Sophie</div>
</article>

<footer class="site-footer">
  <div class="footer-brand">Restwell</div>
  <div class="footer-contact">
    <span><i class="icon-ring"><svg width="16" height="12" viewBox="0 0 16 12"><rect x="1" y="1" width="14" height="10" fill="none" stroke="#fff" stroke-width="1.5"/><path d="M1 1l7 6 7-6" fill="none" stroke="#fff" stroke-width="1.5"/></svg></i>info@restwellclinic.com</span>
    <span><i class="icon-ring"><svg width="14" height="14" viewBox="0 0 14 14"><path d="M3 1l3 3-2 2c1 2 2 3 4 4l2-2 3 3-2 2C6 13 1 8 1 3z" fill="#fff"/></svg></i>1800 555 014</span>
  </div>
  <nav class="footer-nav"><a>HOME</a><a>DIAGNOSIS</a><a>TREATMENT OPTIONS</a><a>ABOUT US</a><a>CONTACT US</a></nav>
  <div class="footer-bar">
    <span>Copyright &copy; 2017 Restwell Clinic. All Right Reserved</span>
    <div class="socials"><i></i><i></i><i></i><i></i><i></i></div>
  </div>
</footer>

</body>
</html>
```